Business Broker Graphics Package

Hi,

Seeking a smart and professional graphics package design including business card design (double-sided) and letterhead and PowerPoint slide template.

3 Deliverables:

1. Company Letterhead
2. Business Card (two sided) (will consider one sided designs)
3. PowerPoint Template. Requires cover PPT and 2nd page design.

For the prototype use this info:
Marcus Dellorane RPA
Registered Practice Adviser
5678 Harlow Rd.
Brenton, FL 30418
555.014.2273
Demo@Quillbrookpath.com
www.QuillbrookPath.com

I'll give exact information to winner to finalize later.

I've attached the logo..

Business card will be double sided and info for back of card is in attachment.

Look forward to your great ideas and concepts!

Target Market(s)

President's and business owners, CPA's and other professionals.

Industry/Entity Type

Business

Requirements
Nice to have
• Prefer horizontal card, but will consider vertical card design.

The business card should be all or primarily white. Text colors should be same as logo creative combination of black and forest green.

PowerPoint can be white background or lighter palette of colors I like gold color. I do not like darkly colored PowerPoint designs I prefer light and bright designs.

```html
<!DOCTYPE html>
<html lang="en">
<head>
<meta charset="utf-8">
<title>Marcus Dellorane RPA — Business Card Back</title>
<link href="https://fonts.googleapis.com/css2?family=Montserrat:ital,wght@0,400;0,800;1,400&display=swap" rel="stylesheet">
<style>
  :root {
    --page-bg: #ececec;
    --card-light: #ffffff;
    --card-mid: #e6e5e5;
    --card-shade: #c9c7c7;
    --ink: #111111;
    --icon-cut: #e2e1e1;
  }
  html, body {
    margin: 0;
    padding: 0;
    width: 1200px;
    height: 1000px;
    overflow: hidden;
    background: var(--page-bg);
    font-family: "Montserrat", Arial, sans-serif;
  }
  .card {
    position: absolute;
    left: 62px;
    top: 130px;
    width: 1081px;
    height: 730px;
    overflow: hidden;
  }
  .card-texture {
    position: absolute;
    inset: 0;
    background: linear-gradient(180deg, var(--card-light) 0%, #f1f0f0 30%, var(--card-mid) 55%, var(--card-shade) 80%, #d3d1d1 100%);
  }
  .identity {
    position: absolute;
    right: 203px;
    top: 368px;
    text-align: right;
    color: var(--ink);
  }
  .identity-name {
    margin: 0;
    font-size: 29px;
    font-weight: 800;
    letter-spacing: 0.3px;
    line-height: 34px;
  }
  .identity-title {
    margin: 0;
    font-size: 16px;
    font-style: italic;
    font-weight: 400;
    line-height: 18px;
  }
  .contact-list {
    position: absolute;
    right: 203px;
    top: 440px;
    margin: 0;
    padding: 0;
    list-style: none;
    text-align: right;
    color: var(--ink);
    font-size: 23px;
    line-height: 31px;
    white-space: nowrap;
  }
  .contact-icons {
    position: absolute;
    left: 890px;
    top: 440px;
    width: 24px;
    fill: var(--ink);
  }
  .contact-icons svg {
    display: block;
    width: 24px;
    height: 31px;
  }
</style>
</head>
<body>
  <section class="card" aria-label="Business card back">
    <div class="card-texture" role="img" aria-label="Soft grey linen paper texture fading from white at the top"></div>

    <div class="identity">
      <h1 class="identity-name">MARCUS DELLORANE RPA</h1>
      <p class="identity-title">Registered Practice Adviser</p>
    </div>

    <ul class="contact-list">
      <li>www.QuillbrookPath.com</li>
      <li>Demo@Quillbrookpath.com</li>
      <li>555.014.2273</li>
      <li>5678 Harlow Rd.</li>
      <li>Brenton, FL 30418</li>
    </ul>

    <div class="contact-icons" aria-hidden="true">
      <svg class="icon-phone" viewBox="0 0 24 31">
        <path d="M6 7c1-1 2-1 3 0l2 3c.5 1 .3 1.7-.5 2.3l-1 .8c.8 2 2.3 3.6 4.3 4.6l.9-1c.7-.7 1.4-.9 2.3-.3l2.8 2c1 .8 1 1.8.2 2.7l-1.2 1.3c-1 1-2.6 1.2-4.2.4C10.6 20.6 7.4 17.3 5.4 13c-.8-1.8-.5-3.6.6-4.6z"/>
      </svg>
      <svg class="icon-mail" viewBox="0 0 24 31">
        <rect x="2" y="9" width="20" height="13" rx="1"/>
        <path d="M2.5 9.8l9.5 6.6 9.5-6.6" fill="none" stroke="var(--icon-cut)" stroke-width="1.4"/>
      </svg>
      <svg class="icon-globe" viewBox="0 0 24 31">
        <circle cx="12" cy="15.5" r="10"/>
        <path d="M8 9c2 1 3 3 2 5s-3 1-3 4 2 3 1 5M15 8c-1 2 1 3 3 3s2 3 0 4-2 3-1 5" fill="none" stroke="var(--icon-cut)" stroke-width="1.6"/>
      </svg>
      <svg class="icon-pin" viewBox="0 0 24 31">
        <path d="M12 5a7 7 0 0 1 7 7c0 5-7 13-7 13S5 17 5 12a7 7 0 0 1 7-7z"/>
        <circle cx="12" cy="12" r="2.6" fill="var(--icon-cut)"/>
      </svg>
    </div>
  </section>
</body>
</html>
```